Brightwave Reach - Business Card

We need a business card for a Social Media Marketing company that specializes in online marketing for small businesses in Canada using common Social Media platforms such as Pixlora, Chatterly, Blinkpost & Quibber.

I have uploaded a copy of our logo which I would like utilized in the business card. We would like the business card to be modern yet classy design.

Our website is www.brightwavereach.ca

Industry/Entity Type

Marketing

Contact Information for Business Card

Email: info@brightwavereach.ca
Website: www.brightwavereach.ca
Telephone: 604-555-0193

Colors

Designer to choose colors to be used in the design.

Requirements
Must have
• Social Media icons on reverse
• Please add some designs with color.

```html
<!DOCTYPE html>
<html lang="en">
<head>
<meta charset="utf-8">
<title>Brightwave Reach – Business Card</title>
<link rel="stylesheet" href="https://fonts.googleapis.com/css2?family=Open+Sans:wght@400;600;700;800&display=swap">
<style>
  :root {
    --backdrop: #1e1e1e;
    --card: #ffffff;
    --ink: #3a3a3a;
    --ink-soft: #7a7a7a;
    --rule: #444444;
  }
  * { margin: 0; padding: 0; box-sizing: border-box; }
  html, body {
    width: 1200px;
    height: 1000px;
    overflow: hidden;
    background: var(--backdrop);
    font-family: "Open Sans", Arial, sans-serif;
  }
  .stage {
    width: 1200px;
    height: 1000px;
    display: flex;
    flex-direction: column;
    align-items: center;
    justify-content: center;
    gap: 40px;
  }
  .card {
    position: relative;
    width: 760px;
    height: 434px;
    background: var(--card);
    border-radius: 36px;
    color: var(--ink);
  }

  /* brand wordmark */
  .brand {
    display: flex;
    align-items: center;
    gap: 14px;
  }
  .brand-square {
    width: 22px;
    height: 22px;
    background: var(--ink);
  }
  .brand-name {
    font-weight: 800;
    font-size: 34px;
    letter-spacing: 0.5px;
    text-transform: uppercase;
    color: var(--ink);
    line-height: 1;
  }

  /* front side */
  .card-front .brand {
    position: absolute;
    left: 50%;
    top: 180px;
    transform: translateX(-50%);
  }
  .social-list {
    position: absolute;
    left: 0;
    right: 0;
    top: 330px;
    display: flex;
    justify-content: center;
    gap: 18px;
    list-style: none;
    font-size: 13px;
    font-weight: 600;
    color: var(--ink);
  }

  /* back side */
  .card-back .brand {
    position: absolute;
    right: 56px;
    top: 140px;
  }
  .card-back .brand-name { font-size: 26px; }
  .card-back .brand-square { width: 18px; height: 18px; }
  .person {
    position: absolute;
    left: 56px;
    top: 150px;
  }
  .person-name {
    font-weight: 700;
    font-size: 32px;
    letter-spacing: 0.5px;
    text-transform: uppercase;
    color: var(--ink);
    line-height: 1.05;
  }
  .person-title {
    font-size: 22px;
    font-weight: 400;
    color: var(--ink-soft);
    padding-left: 12px;
    line-height: 1.1;
  }
  .person-rule {
    width: 44px;
    height: 3px;
    background: var(--rule);
    margin: 14px 0 0 12px;
  }
  .contact-list {
    position: absolute;
    left: 56px;
    bottom: 46px;
    list-style: none;
    font-size: 15px;
    color: var(--ink);
  }
  .contact-list li {
    display: flex;
    align-items: center;
    gap: 12px;
    line-height: 26px;
  }
  .contact-list svg { width: 14px; height: 14px; fill: var(--ink); }
  .contact-list strong { font-weight: 700; }
</style>
</head>
<body>
<main class="stage">

  <section class="card card-front" aria-label="Card front">
    <div class="brand">
      <span class="brand-square"></span>
      <span class="brand-name">Brightwave Reach</span>
    </div>
    <ul class="social-list">
      <li>Chatterly</li>
      <li>Quibber</li>
      <li>Pixlora</li>
      <li>Blinkpost</li>
    </ul>
  </section>

  <section class="card card-back" aria-label="Card back">
    <div class="person">
      <h1 class="person-name">Daniel Reyes</h1>
      <p class="person-title">Precedent</p>
      <div class="person-rule"></div>
    </div>

    <div class="brand">
      <span class="brand-square"></span>
      <span class="brand-name">Brightwave Reach</span>
    </div>

    <ul class="contact-list">
      <li>
        <svg viewBox="0 0 16 16" aria-hidden="true"><path d="M3.5 1.5l2.5 0 1 3.5-1.6 1.2a9 9 0 0 0 4.4 4.4L11 9l3.5 1v2.5c0 1-1 2-2 2A11 11 0 0 1 1.5 3.5c0-1 1-2 2-2z"/></svg>
        <span>604-555-0193</span>
      </li>
      <li>
        <svg viewBox="0 0 16 16" aria-hidden="true"><path d="M1 3h14v10H1z M2 4.2v.6l6 4 6-4v-.6z" fill-rule="evenodd"/></svg>
        <span>info@brightwavereach.ca</span>
      </li>
      <li>
        <svg viewBox="0 0 16 16" aria-hidden="true"><circle cx="8" cy="8" r="7"/></svg>
        <span>www.<strong>brightwavereach</strong>.ca</span>
      </li>
    </ul>
  </section>

</main>
</body>
</html>
```